Aunt Wilma's Ember-Kissed Husk Shack Concession Trailer Logo Wraps

Looking to put my design concept into a final production-ready format for vinyl-based logo "wrap" on the exterior of a 7x12 black concession trailer selling farm-fresh corn on the cob slathered in flavor flamboyance, corn in a cup, corn over crushed snacks (Crunvels, Zaplins, Puffnars, etc.) served in the bags, fire-roasted street corn (Mexican elotes), corn grits, corn chowder, cornbread, corndogs. I have my fonts and colors and a flame graphic I've roughly edited/reworked attempting to make it work and need a design pro to bring it all together for me. The approximate size of the graphics on the four sides of the trailer will be: the serving window when closed (48"L x 24"H); front (48"x48"); full right side (11'x5'); door (6'x2') and possibly the left side next to door (3'x5'). Pictures uploaded.
Target Market(s)
Food truck festivals, private catering gigs, fairs, farm markets, concerts, etc.
Font styles to use
Other font styles liked:
- flame fetish, Algerian
Requirements
Must have
- My color scheme as depicted in uploaded files, flame fetish font uploaded (will consider similar fonts), flame/fire artwork, bright bold colors that pop against a black background
Nice to have
- straight line of flames on each side of the "fire-roasted" text, flowing from the first and last letter

```html
<!DOCTYPE html>
<html lang="en">
<head>
<meta charset="utf-8">
<title>Aunt Wilma's Ember-Kissed Husk Shack</title>
<link rel="stylesheet" href="https://fonts.googleapis.com/css2?family=Great+Vibes&family=Kaushan+Script&family=Cinzel:wght@900&family=Lato:wght@700;900&display=swap">
<style>
  :root {
    --bg: #000000;
    --cyan: #12e6f0;
    --sky: #1fb4ff;
    --yellow: #f5e11c;
    --flame-deep: #b8250a;
    --flame-mid: #f07a12;
    --flame-hot: #ffc93a;
    --ember-glow: #ff8a1a;
    --white: #ffffff;
  }
  * { margin: 0; padding: 0; box-sizing: border-box; }
  html, body { width: 1200px; height: 2581px; overflow: hidden; background: var(--bg); }
  .wrap-panel { position: relative; width: 1200px; height: 2581px; background: var(--bg); overflow: hidden; }

  .flame-band {
    position: absolute; left: 0; top: 560px; width: 1200px; height: 305px;
    background:
      radial-gradient(ellipse 22% 90% at 4% 100%, var(--flame-hot), rgba(240,122,18,0.7) 45%, transparent 80%),
      radial-gradient(ellipse 22% 90% at 96% 100%, var(--flame-hot), rgba(240,122,18,0.7) 45%, transparent 80%),
      radial-gradient(ellipse 60% 70% at 50% 100%, rgba(255,160,40,0.85), rgba(184,37,10,0.55) 55%, transparent 85%),
      linear-gradient(to bottom, transparent 0%, rgba(184,37,10,0.35) 55%, rgba(240,122,18,0.8) 100%);
  }
  .smoke-band {
    position: absolute; left: 22px; top: 864px; width: 1178px; height: 100px;
    background: linear-gradient(to bottom, rgba(70,55,40,0.75), rgba(0,0,0,0));
  }

  .headline { position: absolute; left: 0; width: 1200px; text-align: center; white-space: nowrap; }
  .owner-name {
    top: 525px; font-family: "Great Vibes", cursive; font-size: 190px; line-height: 1;
    color: var(--cyan); text-shadow: 3px 3px 0 #05343a;
  }
  .style-line {
    top: 710px; font-family: "Kaushan Script", "Great Vibes", cursive; font-size: 150px; line-height: 1;
    color: #000;
    text-shadow: 0 0 6px var(--ember-glow), 0 0 14px var(--ember-glow), 0 0 26px var(--flame-mid);
  }
  .shack-word {
    font-family: "Cinzel", serif; font-weight: 900; line-height: 1;
    color: var(--yellow); text-shadow: -4px 5px 0 #000, -8px 9px 0 var(--yellow);
  }
  .shack-word.first { top: 915px; font-size: 235px; letter-spacing: 4px; }
  .shack-word.second { top: 1175px; font-size: 235px; letter-spacing: 4px; }

  .tagline { position: absolute; left: 0; width: 1200px; text-align: center; white-space: nowrap; font-family: "Great Vibes", cursive; line-height: 1; font-weight: 400; }
  .tagline.one { top: 1478px; font-size: 100px; color: var(--cyan); text-shadow: 1px 1px 0 var(--cyan); }
  .tagline.two { top: 1585px; font-size: 92px; color: var(--sky); text-shadow: 1px 1px 0 var(--sky); }

  .events-note {
    position: absolute; left: 0; top: 1945px; width: 1220px; text-align: center;
    font-family: "Lato", sans-serif; font-weight: 900; font-size: 45px; letter-spacing: 1px; color: var(--white);
  }
  .social-row {
    position: absolute; left: 147px; top: 2060px; width: 900px; display: flex; align-items: center; justify-content: space-between;
    font-family: "Lato", sans-serif; font-weight: 700; font-size: 26px; color: var(--white); white-space: nowrap;
  }
  .social-name { display: flex; align-items: center; gap: 8px; }
  .social-name .mark { width: 20px; height: 20px; background: var(--white); display: inline-block; }
  .tags { display: flex; gap: 20px; }
</style>
</head>
<body>
  <main class="wrap-panel">
    <div class="flame-band" role="img" aria-label="Band of realistic orange and yellow fire flames across the panel"></div>
    <div class="smoke-band"></div>

    <h1 class="headline owner-name">Aunt Wilma's</h1>
    <p class="headline style-line">ember-kissed</p>
    <p class="headline shack-word first">HUSK</p>
    <p class="headline shack-word second">SHACK</p>

    <p class="tagline one">Corn on the cob</p>
    <p class="tagline two">slathered in sizzling swagger!</p>

    <p class="events-note">AVAILABLE FOR PRIVATE EVENTS</p>
    <div class="social-row">
      <span>Follow us on</span>
      <span class="social-name"><span class="mark"></span>Chatterbook</span>
      <span class="social-name">Snapgrid</span>
      <span class="tags"><span>#aunt_wilma</span><span>#emberkissedeats</span></span>
    </div>
  </main>
</body>
</html>
```